female esthetician looking for an impact business card

I an an expert in skin care industry with high experience in NYC.I want my business card to look professional , an impact at first look. I do want a combination between white and gold . I believe the font will be great if is gold.. The Fonts are also important. MIRABELA COSTINA (SKIN CARE BOUTIQUE)

THIS SHOULD BE THE BUSINESS NAME, and should be placed on th eback of the card.
IN front m, the name MIRABELA COSTINA - ESTHETCIAN

BY APPOINTMENTS ONLY: 518.240.7136

Target Market(s)

HIGH END CLIENTELE

Contact Information for Business Card

iT WILL BE on a luxury paper. I neeed the wow feeling

Requirements
Should not have
• pictures

```html
<!DOCTYPE html>
<html lang="en">
<head>
<meta charset="utf-8">
<title>Mirabela Costina – Skin Care Boutique Business Card</title>
<link rel="stylesheet" href="https://fonts.googleapis.com/css2?family=Cinzel:wght@400;600&family=Lato:wght@300;400&display=swap">
<style>
  :root {
    --backdrop: #1b1b1b;
    --card: #121212;
    --card-edge: #1f1f1f;
    --gold: #f2b51c;
    --silver: #d9d9d9;
    --text-light: #e6e6e6;
    --text-muted: #9a9a9a;
    --rule: #5a5a5a;
  }
  * { box-sizing: border-box; margin: 0; padding: 0; }
  html, body { width: 1200px; height: 900px; overflow: hidden; }
  body {
    background: var(--backdrop);
    font-family: "Lato", sans-serif;
    display: flex;
    flex-direction: column;
    align-items: center;
    justify-content: center;
    gap: 50px;
  }
  .card {
    position: relative;
    width: 620px;
    height: 354px;
    border-radius: 22px;
    background: var(--card);
    border: 1px solid var(--card-edge);
    box-shadow: 0 18px 40px rgba(0,0,0,.6);
  }
  /* Back */
  .card-back { display: flex; align-items: center; justify-content: center; }
  .back-brand {
    display: flex; align-items: center; gap: 16px;
    font-family: "Cinzel", serif; font-weight: 400;
    font-size: 34px; letter-spacing: 4px; color: var(--silver);
  }
  .brand-square { width: 14px; height: 14px; background: var(--silver); }
  /* Front */
  .front-brand {
    position: absolute; right: 46px; top: 60px; text-align: right;
  }
  .front-brand .brand-row {
    display: flex; align-items: center; justify-content: flex-end; gap: 12px;
  }
  .front-brand .brand-square { width: 12px; height: 12px; background: var(--gold); }
  .brand-name {
    font-family: "Cinzel", serif; font-size: 30px; letter-spacing: 3px; color: var(--gold);
  }
  .brand-tagline {
    margin-top: 6px; font-size: 10px; letter-spacing: 8px; color: var(--text-muted);
    text-transform: uppercase;
  }
  .divider {
    position: absolute; left: 280px; right: 46px; top: 150px;
    height: 1px; background: var(--rule);
  }
  .person { position: absolute; left: 46px; top: 176px; }
  .person-name {
    font-family: "Cinzel", serif; font-weight: 600; font-size: 22px;
    letter-spacing: 1px; color: var(--gold);
  }
  .person-title { font-size: 17px; color: var(--text-light); margin-top: 2px; }
  .contact-list { list-style: none; margin-top: 16px; }
  .contact-list li {
    display: flex; align-items: center; gap: 10px;
    font-size: 17px; color: var(--text-light); line-height: 26px;
  }
  .contact-list svg { width: 14px; height: 14px; flex: none; }
  .address {
    position: absolute; right: 46px; top: 178px; text-align: right;
    font-size: 17px; line-height: 24px; color: var(--text-light);
  }
</style>
</head>
<body>
  <section class="card card-back" aria-label="Card back">
    <div class="back-brand"><span class="brand-square"></span>MIRABELA COSTINA</div>
  </section>

  <section class="card card-front" aria-label="Card front">
    <div class="front-brand">
      <div class="brand-row"><span class="brand-square"></span><span class="brand-name">MIRABELA COSTINA</span></div>
      <div class="brand-tagline">Skin Care Expert</div>
    </div>
    <div class="divider"></div>

    <div class="person">
      <div class="person-name">MIRABELA COSTINA</div>
      <div class="person-title">Esthetician</div>
      <ul class="contact-list">
        <li>
          <svg viewBox="0 0 14 14" aria-hidden="true"><path fill="#f2b51c" d="M2 3c0-1 1-2 2-2h6c1 0 2 1 2 2v1H9V3H5v1H2zM3 6h8l1 6H2z"/></svg>
          518.240.7136
        </li>
        <li>
          <svg viewBox="0 0 14 14" aria-hidden="true"><rect x="1" y="3" width="12" height="8" fill="#f2b51c"/><path d="M1 3l6 5 6-5" stroke="#121212" stroke-width="1.2" fill="none"/></svg>
          hello@costinaskin.com
        </li>
        <li>
          <svg viewBox="0 0 14 14" aria-hidden="true"><circle cx="7" cy="7" r="6" fill="#f2b51c"/><path d="M1 7h12M7 1c-3 3-3 9 0 12M7 1c3 3 3 9 0 12" stroke="#121212" stroke-width="1" fill="none"/></svg>
          www.costinaskin.com
        </li>
      </ul>
    </div>

    <address class="address" style="font-style:normal">
      88 Larkspur Avenue, Suite 4<br>New York, NY 10021
    </address>
  </section>
</body>
</html>
```